Luxury travel agency needs a website design

We are a travel agency specializing in booking luxury vacations. We specialize in Hawaii, Europe and Caribbean, but will do all vacations. I want a very classy website design which would attract luxury clients. The company name is "Harbors and Hammocks Travel Agency". Would love the web design to go with the color scheme of the logo. Hex codes included in files. Logo is attached. Would also love more Grey in the website. I want it very elegant

Coding

Coded - Design and coding required

Font styles to use
Sans Serif
Decorative

Requirements
Must have
• - Consultation Tab or a page where the client can fill out a short form about what vacation that they would want to book. I want this info to be sent to me in order for me to contact them.
- Somewhere with my contact info "email: marla@harborsandhammockstravel.example and phone number"
- Social media links
- About section "Marla Dunbevy - Agency Owner (picture provided)
Marla has been traveling full time for the passed two years and has been very passionate about travel from a young age. Marla is dedicated to working closely with clients to book their dream vacation.
Marla's specializations include honeymoons and anniversaries focusing on travel in Europe, Hawaii and all inclusive resorts in the Caribbean.

```html
<!DOCTYPE html>
<html lang="en">
<head>
<meta charset="utf-8">
<title>Harbors and Hammocks Travel Agency – Contact</title>
<link href="https://fonts.googleapis.com/css2?family=Open+Sans:wght@400;600;700&family=Original+Surfer&display=swap" rel="stylesheet">
<style>
  :root{
    --orange:#f0915a;
    --ink:#1c1c1c;
    --text:#3a3a3a;
    --grey-bg:#f3f3f3;
    --line:#d9d9d9;
    --white:#ffffff;
    --footer:#0d0d0d;
  }
  *{box-sizing:border-box;margin:0;padding:0}
  html,body{width:1200px;height:2540px;overflow:hidden}
  body{position:relative;background:var(--white);font-family:'Open Sans',Arial,sans-serif;color:var(--text)}
  .abs{position:absolute}

  /* top bar */
  .top-bar{left:0;top:0;width:1200px;height:28px;background:var(--orange);color:var(--white);font-size:12px;display:flex;align-items:center;justify-content:space-between;padding:0 170px 0 172px}
  .top-bar span{display:flex;align-items:center;gap:8px}
  .social{display:flex;gap:6px}
  .social i{width:16px;height:16px;border-radius:50%;background:var(--white);display:block}

  /* hero */
  .hero{left:0;top:28px;width:1200px;height:520px}
  .brand{left:160px;top:118px;width:300px;color:var(--white);font-family:'Original Surfer',cursive;font-size:26px;line-height:1.1;text-align:center;white-space:nowrap}
  .brand small{display:block;font-size:12px;letter-spacing:3px}
  .nav{left:550px;top:100px;display:flex;gap:34px;align-items:center;color:var(--white);font-size:13px;font-weight:600}
  .nav .cta{background:var(--ink);padding:10px 16px;border-radius:20px;font-size:12px}
  .hero-title{left:660px;top:228px;width:370px;text-align:right;font-family:'Original Surfer',cursive;font-size:56px;color:var(--white);white-space:nowrap}

  /* contact form */
  .form-section{left:0;top:520px;width:1200px;height:1140px;background:var(--grey-bg)}
  .heading{font-family:'Original Surfer',cursive;font-size:38px;color:var(--ink);text-align:center;width:1200px;left:0}
  .heading em{font-style:normal;color:var(--orange)}
  .lead{left:0;top:738px;width:1200px;text-align:center;font-size:15px}
  .field{background:var(--white);border:2px solid var(--line);border-radius:22px;font-size:14px;color:var(--text);padding:0 20px;display:flex;align-items:center}
  .field.area{align-items:flex-start;padding-top:18px}
  .btn{background:var(--orange);color:var(--white);font-size:13px;font-weight:700;border-radius:26px;display:flex;align-items:center;justify-content:center}

  .deco-hat{left:935px;top:1150px;width:130px;height:100px;background:radial-gradient(closest-side,rgba(214,178,120,.5),rgba(214,178,120,.18) 60%,rgba(214,178,120,0))}
  .deco-camera{left:585px;top:1545px;width:110px;height:90px;background:radial-gradient(closest-side,rgba(90,90,90,.28),rgba(90,90,90,.1) 60%,rgba(90,90,90,0))}

  .card{left:170px;top:1280px;width:860px;height:250px;background:var(--white);border-radius:36px;box-shadow:0 6px 14px rgba(0,0,0,.18)}
  .contact-item{display:flex;align-items:center;gap:14px;font-size:14px;color:var(--ink);white-space:nowrap}
  .icon{width:44px;height:44px;border-radius:50%;background:var(--orange);display:flex;align-items:center;justify-content:center}

  /* banner */
  .banner{left:0;top:1655px;width:1200px;height:460px}
  .banner-name{left:0;top:1790px;width:1200px;text-align:center;color:var(--white);font-family:'Original Surfer',cursive;font-size:64px;line-height:1.1}
  .banner-name small{display:block;font-size:26px;letter-spacing:8px}

  /* footer */
  .footer{left:0;top:2110px;width:1200px;height:430px;background:var(--footer)}
  .footer-brand{left:160px;top:2278px;width:340px;text-align:center;color:var(--white);font-family:'Original Surfer',cursive;font-size:28px;line-height:1.1;white-space:nowrap}
  .footer-brand small{display:block;font-size:12px;letter-spacing:3px}
  .col-title{color:var(--white);font-size:14px;font-weight:600;letter-spacing:.5px}
  .links{left:570px;top:2170px;color:var(--white);font-size:13px;line-height:23px}
  .links li{list-style:none}
  .rule{left:170px;top:2440px;width:860px;height:1px;background:#444}
  .copyright{left:0;top:2474px;width:1200px;text-align:center;color:var(--white);font-size:12px}
</style>
</head>
<body>

<div class="abs top-bar">
  <span><svg width="14" height="10" viewBox="0 0 14 10"><rect x=".5" y=".5" width="13" height="9" fill="none" stroke="#fff"/><path d="M.5 .5 7 6l6.5-5.5" fill="none" stroke="#fff"/></svg>marla@harborsandhammockstravel.example</span>
  <span><svg width="12" height="12" viewBox="0 0 24 24"><path fill="#fff" d="M6.6 10.8a15 15 0 0 0 6.6 6.6l2.2-2.2a1 1 0 0 1 1-.25 11 11 0 0 0 3.6.6 1 1 0 0 1 1 1V20a1 1 0 0 1-1 1A17 17 0 0 1 3 4a1 1 0 0 1 1-1h3.5a1 1 0 0 1 1 1c0 1.25.2 2.45.6 3.6a1 1 0 0 1-.25 1z"/></svg>(555)014-2290 <span class="social" aria-label="Social media links"><i></i><i></i><i></i></span></span>
</div>

<svg class="abs hero" width="1200" height="520" viewBox="0 0 1200 520" role="img" aria-label="Photo of a tropical beach at sunset with rocks and palm leaves">
  <defs>
    <linearGradient id="sky" x1="0" y1="0" x2="0" y2="1">
      <stop offset="0" stop-color="#5a6f93"/>
      <stop offset=".45" stop-color="#d99a9a"/>
      <stop offset=".62" stop-color="#f4c08d"/>
      <stop offset=".75" stop-color="#6f7e93"/>
      <stop offset="1" stop-color="#2f3b45"/>
    </linearGradient>
  </defs>
  <rect width="1200" height="520" fill="url(#sky)"/>
  <path d="M0 420 C240 520 420 470 640 470 C860 470 1000 390 1200 360 L1200 520 L0 520Z" fill="var(--grey-bg)"/>
</svg>

<div class="abs brand">Harbors &amp; Hammocks<small>TRAVEL AGENCY</small></div>
<nav class="abs nav"><span>HOME</span><span>ABOUT</span><span>CONTACT</span><span class="cta">SCHEDULE A CONSULT</span></nav>
<h1 class="abs hero-title">Contact Us</h1>

<section class="abs form-section" aria-label="Contact form"></section>

<svg class="abs" style="left:0;top:520px" width="1200" height="1140" viewBox="0 0 1200 1140" fill="none" stroke="var(--orange)" stroke-width="2" stroke-dasharray="6 6">
  <path d="M770 20 C760 80 790 130 760 160"/>
  <path d="M1040 665 C1090 630 1150 590 1200 560"/>
  <path d="M440 1120 C510 1060 560 1065 600 1060"/>
</svg>

<h2 class="abs heading" style="top:652px">Contact <em>Form</em></h2>
<p class="abs lead">Please leave your information below and we will contact you for further inquiries</p>

<div class="abs field" style="left:165px;top:825px;width:425px;height:62px">First Name</div>
<div class="abs field" style="left:607px;top:825px;width:425px;height:62px">Last Name</div>
<div class="abs field" style="left:165px;top:905px;width:425px;height:62px">Email Address</div>
<div class="abs field" style="left:607px;top:905px;width:425px;height:62px">Phone Number</div>
<div class="abs field area" style="left:165px;top:985px;width:867px;height:120px">Message</div>
<div class="abs btn" style="left:538px;top:1135px;width:124px;height:52px">SUBMIT</div>

<div class="abs deco-hat" role="img" aria-label="Illustration of a straw sun hat"></div>

<div class="abs card"></div>
<h2 class="abs heading" style="top:1318px">Contact <em>Us</em></h2>
<div class="abs contact-item" style="left:310px;top:1428px">
  <span class="icon"><svg width="20" height="14" viewBox="0 0 20 14"><rect x="1" y="1" width="18" height="12" fill="none" stroke="#fff" stroke-width="2"/><path d="M1 1l9 7 9-7" fill="none" stroke="#fff" stroke-width="2"/></svg></span>
  marla@harborsandhammockstravel.example
</div>
<div class="abs contact-item" style="left:720px;top:1428px">
  <span class="icon"><svg width="20" height="20" viewBox="0 0 24 24"><path fill="#fff" d="M6.6 10.8a15 15 0 0 0 6.6 6.6l2.2-2.2a1 1 0 0 1 1-.25 11 11 0 0 0 3.6.6 1 1 0 0 1 1 1V20a1 1 0 0 1-1 1A17 17 0 0 1 3 4a1 1 0 0 1 1-1h3.5a1 1 0 0 1 1 1c0 1.25.2 2.45.6 3.6a1 1 0 0 1-.25 1z"/></svg></span>
  (555)014-2290
</div>

<div class="abs deco-camera" role="img" aria-label="Illustration of a vintage camera"></div>

<svg class="abs banner" width="1200" height="460" viewBox="0 0 1200 460" role="img" aria-label="Photo of a tropical island coastline at sunset">
  <defs>
    <linearGradient id="isle" x1="0" y1="0" x2="0" y2="1">
      <stop offset="0" stop-color="#2d3f4e"/>
      <stop offset=".35" stop-color="#8a7e78"/>
      <stop offset=".55" stop-color="#e7a56b"/>
      <stop offset=".7" stop-color="#3e5a3d"/>
      <stop offset="1" stop-color="#2d6f86"/>
    </linearGradient>
  </defs>
  <rect width="1200" height="460" fill="url(#isle)"/>
  <path d="M0 455 C300 380 700 380 1200 415 L1200 460 L0 460Z" fill="var(--orange)"/>
</svg>
<div class="abs banner-name">Harbors &amp; Hammocks<small>TRAVEL AGENCY</small></div>

<footer class="abs footer"></footer>
<div class="abs footer-brand">Harbors &amp; Hammocks<small>TRAVEL AGENCY</small></div>

<div class="abs links">
  <div class="col-title" style="margin-bottom:14px">QUICK LINKS</div>
  <ul><li>Home</li><li>About Us</li><li>Contact Us</li><li>Schedule a Consult</li></ul>
</div>

<div class="abs col-title" style="left:780px;top:2170px;width:250px;line-height:20px">SUBSCRIBE TO OUR NEWSLETTER</div>
<div class="abs field" style="left:780px;top:2226px;width:248px;height:54px;border:none">Email</div>
<div class="abs btn" style="left:780px;top:2300px;width:124px;height:52px;font-weight:600">Subscribe</div>

<div class="abs rule"></div>
<p class="abs copyright">Copyright @ 2021 Harbors and Hammocks. All Rights Reserved.</p>

</body>
</html>
```